Yoga Workshop - Yoga Practice information flyer

I am a yoga teacher who will be presenting a workshop on yoga for sleep and need a brochure for my clients which outlines a practice that I give them so they can do the practice at home. Ideally I would like a brochure that is a single A3 size of paper in size that folds in half to an A4 booklet with the entire practice on the centre section to make it easy for people to do the practice at home with just one open page in front of them:
* Front page detailing "Yoga for Sleep Workshop" and "Restorative Yoga Practice"
* Centre contains the information on the practice contained in the attached word document. The practice consists of 5 postures, so there needs to be five separate sections which have the pictures of the postures (attached in uploaded files) and the wording contained in the attached word document. All pictures uploaded need to be included in the flyer as each posture has different pictures demonstrating the posture using yoga props or using things people have at home
* Back page containing a picture of myself (picture uploaded in files) with some information about me (contained in the attached word document) and my website www.calmdrift.com.au

I also need this flyer to be able to printed on 2 double sided A4 sheets of paper so will require 2 x pdf file versions. Importantly, for the centre section of the flyer, the design needs to ensure if it is printed on A4 paper, the wording and pictures for each of the postures are not separated over two pages

Target Market(s)

Existing clients

Requirements
Must have
• Detailed in project description
Nice to have
• The word document also contains some quotes. These do not need to be included in the flyer. If there is room and there is room for one or two of those please include where it would look good
Should not have
• Stock pictures of people in yoga postures which a normal everyday person could not get into

```html
<!DOCTYPE html>
<html lang="en">
<head>
<meta charset="utf-8">
<title>Yoga for Sleep Workshop – Booklet</title>
<link rel="stylesheet" href="https://fonts.googleapis.com/css2?family=Josefin+Sans:wght@300;400;600&family=Libre+Baskerville:wght@700&family=Parisienne&display=swap">
<style>
  :root{
    --navy:#2f3a5c;
    --orange:#d07f55;
    --orange-soft:#e3a27f;
    --ink:#5a5a5a;
    --paper:#ffffff;
    --backdrop:#e8e6e2;
  }
  *{box-sizing:border-box;margin:0;padding:0}
  html,body{width:1200px;height:900px;overflow:hidden;background:var(--backdrop)}
  body{position:relative;font-family:"Josefin Sans",sans-serif;color:var(--ink)}

  .page{position:absolute;top:188px;height:523px;background:var(--paper);overflow:hidden;box-shadow:0 2px 10px rgba(0,0,0,.12)}
  .cover{left:30px;width:370px}
  .spread{left:430px;width:740px}
  .spread::after{content:"";position:absolute;left:369px;top:0;width:2px;height:100%;background:linear-gradient(90deg,rgba(0,0,0,.06),rgba(0,0,0,0))}

  /* cover */
  .cover-photo{position:absolute;left:0;top:0;width:370px;height:430px;background:linear-gradient(180deg,#c9d6dc 0%,#6f8f58 38%,#8c8a5a 70%,#a59870 100%)}
  .cover-wave{position:absolute;left:0;top:0}
  .brand{position:absolute;left:0;width:100%;text-align:center;font-family:"Libre Baskerville",serif;font-weight:700;color:var(--navy)}
  .cover .brand-mark{position:absolute;left:172px;top:12px;width:26px;height:26px;border-radius:50%;border:2px solid var(--orange)}
  .cover .brand{top:70px;font-size:19px}
  .tagline{position:absolute;left:0;width:100%;text-align:center;font-size:7px;letter-spacing:1.4px;color:var(--navy)}
  .cover .tagline{top:99px}
  .cover-title{position:absolute;left:0;top:447px;width:100%;text-align:center;color:#fff;font-weight:300;font-size:27px}
  .cover-sub{position:absolute;left:0;top:482px;width:100%;text-align:center;color:var(--orange-soft);font-family:"Parisienne",cursive;font-size:21px}

  /* spread */
  .intro{position:absolute;left:26px;top:37px;width:327px;height:120px;background:var(--orange);border-radius:5px;padding:12px 12px;color:#fff}
  .intro h1{font-weight:400;font-size:15px;margin-bottom:6px}
  .intro p{font-size:6.4px;line-height:1.45;font-weight:300}

  .posture{position:absolute;width:327px;border:1px solid var(--orange-soft);border-radius:5px}
  .posture-photo{position:absolute;left:-8px;top:18px;width:78px;height:78px;border-radius:50%;border:3px solid #fff;box-shadow:0 0 0 1px #eee;background:radial-gradient(circle at 50% 45%,#b23a3a 0 18%,#3f7ab8 19% 34%,#9b5b2e 35% 100%)}
  .posture h2{position:absolute;left:80px;top:-1px;width:222px;height:14px;line-height:15px;padding-left:5px;background:var(--orange);color:#fff;border-radius:0 8px 8px 0;font-size:7.4px;font-weight:400}
  .posture h2 b{font-weight:600}
  .posture-body{position:absolute;left:80px;top:18px;right:8px;font-size:5.9px;line-height:1.38}
  .posture-body p{margin-bottom:3px}
  .label{color:var(--orange)}

  .p1{left:26px;top:167px;height:120px}
  .p2{left:26px;top:298px;height:120px}
  .p3{left:387px;top:32px;height:120px}
  .p4{left:387px;top:167px;height:120px}
  .p5{left:387px;top:298px;height:100px}

  .spread-wave{position:absolute;left:0;top:0}
  .spread .brand{top:443px;width:370px;font-size:15px}
  .spread .tagline{top:466px;width:370px;font-size:5.6px;letter-spacing:1px}

  .quote{position:absolute;right:26px;width:190px;text-align:right;color:#fff;font-size:7px;font-style:italic;font-weight:300;line-height:1.7}
  .quote .mark{color:var(--orange);font-family:"Libre Baskerville",serif;font-size:18px;font-style:normal;vertical-align:-6px;margin-right:4px}
  .q1{top:445px}
  .q2{top:484px}
</style>
</head>
<body>

<section class="page cover">
  <div class="cover-photo" role="img" aria-label="Photo of the teacher seated cross-legged in meditation on a grassy lawn with tropical trees behind"></div>
  <svg class="cover-wave" width="370" height="523" viewBox="0 0 370 523" aria-hidden="true">
    <path d="M0,405 C90,380 200,395 370,405 L370,523 L0,523 Z" fill="#fff" opacity=".9"/>
    <path d="M0,420 C100,398 230,420 370,405 L370,523 L0,523 Z" fill="var(--navy)"/>
  </svg>
  <span class="brand-mark"></span>
  <div class="brand">Calm Drift Yoga</div>
  <div class="tagline">Be the change you wish to see in the world</div>
  <div class="cover-title">Yoga for Sleep Workshop</div>
  <div class="cover-sub">Restorative Yoga Practice</div>
</section>

<section class="page spread">
  <svg class="spread-wave" width="740" height="523" viewBox="0 0 740 523" aria-hidden="true">
    <path d="M0,478 C120,470 260,500 370,500 C480,498 620,440 740,408 L740,523 L0,523 Z" fill="#dfe2ea"/>
    <path d="M0,488 C120,480 270,510 370,508 C500,504 620,452 740,418 L740,523 L0,523 Z" fill="#fff"/>
    <path d="M0,496 C130,490 270,518 370,515 C510,508 620,462 740,428 L740,523 L0,523 Z" fill="var(--navy)"/>
    <path d="M370,523 C450,470 560,440 740,410 L740,523 Z" fill="var(--navy)"/>
  </svg>

  <div class="intro">
    <h1>Yoga for Sleep Workshop</h1>
    <p>Use this sequence to relax and unwind at the end of a day or before bed. Settle comfortably into each posture for about 5-7 minutes. Set a timer to let you know when it is time to change position, and you can also listen to any music you find relaxing at the same time. The audio recording from the Yoga for Sleep Workshop can also be used to recreate the practice at home. In the middle of the night when you can't sleep, you might like to try getting up and resting in any one of these postures for about 5-10 minutes before heading back to bed.</p>
  </div>

  <article class="posture p1">
    <div class="posture-photo" role="img" aria-label="Photo of supported chest opening pose with knee support on a yoga mat"></div>
    <h2><b>POSTURE 1</b> – Supported Chest Opening with Knee Support</h2>
    <div class="posture-body">
      <p><span class="label">PROPS</span> – 2 x bolsters (or towels rolled up lengthways), 1 x cushion for head support (optional)</p>
      <p><span class="label">SET UP NOTES</span> – Position the props in a T-position with one bolster/towel running parallel to the yoga mat and one bolster/towel running horizontal to the mat underneath the knees. Position yourself so your buttocks is on the floor and the parallel bolster runs from the lower back up to behind the head.</p>
      <p><span class="label">CAUTION</span> – If any lower back pain is experienced adjust the parallel bolster height by using a towel. If using a towel, the height of the parallel support prop can be adjusted by either using a thinner towel or loosely rolling the towel. Do not use any parallel support prop if pain continues.</p>
    </div>
  </article>

  <article class="posture p2">
    <div class="posture-photo" role="img" aria-label="Photo of supported bound-angle pose with blocks under the knees"></div>
    <h2><b>POSTURE 2</b> – Supported Bound-Angle Pose</h2>
    <div class="posture-body">
      <p><span class="label">PROPS</span> – 1 x bolsters (or towel rolled up lengthways), 2 x yoga blocks/bolsters (or pillows), 1 x cushion for head support (optional)</p>
      <p><span class="label">SET UP NOTES</span> – Similar to Posture 1 without the bolster behind the knees. Instead, the soles of the feet are together with knees wide being supported by either blocks, bolsters or pillows.</p>
      <p><span class="label">CAUTION</span> – If any lower back pain is experienced adjust the parallel bolster height by using a towel. If using a towel, the height of the parallel support prop can be adjusted by either using a thinner towel or loosely rolling the towel. Do not use any parallel support prop if pain continues.</p>
    </div>
  </article>

  <div class="brand">Calm Drift Yoga</div>
  <div class="tagline">Be the change you wish to see in the world</div>

  <article class="posture p3">
    <div class="posture-photo" role="img" aria-label="Photo of elevated legs-up-the-wall pose"></div>
    <h2><b>POSTURE 3</b> – Elevated Legs-Up-the-Wall Pose</h2>
    <div class="posture-body">
      <p><span class="label">PROPS</span> – 1 x bolsters (or towel or blanket densely folded to a width of about 15-30cm), 1 x cushion for head support (optional)</p>
      <p><span class="label">SET UP NOTES</span> – To enter the posture sit at 90 degrees to the wall with the side of your hip about a hand width away from the wall, and the bolster/folded towel or blanket close by. Lie down on the mat on your side then roll onto your back and extend feet up the wall. The feet can push into the wall to elevate the hips slightly so the bolster/folded towel or blanket can slide underneath the hips. The prop should be positioned underneath the sacrum (flat bony structure at the base of the spine).</p>
      <p><span class="label">CAUTION</span> – If any lower back pain is experienced adjust the height the hips are elevated by using a towel or blanket that is folded to a lower height. Remove the prop if pain continues.</p>
    </div>
  </article>

  <article class="posture p4">
    <div class="posture-photo" role="img" aria-label="Photo of supported child's pose over a bolster"></div>
    <h2><b>POSTURE 4</b> – Supported Child's Pose</h2>
    <div class="posture-body">
      <p><span class="label">PROPS</span> – 1-2 x bolsters (or 3-4 bed pillows)</p>
      <p><span class="label">SET UP NOTES</span> – Position bolster or stacked pillows under torso. Rest the head in one direction and remember to turn to the head to the other side half way through the time you spend in this posture.</p>
      <p><span class="label">CAUTION</span> – If any knee or hip pain is experienced, increase the height of the support under the torso by adding more bolsters, folded blankets or pillows.</p>
    </div>
  </article>

  <article class="posture p5">
    <div class="posture-photo" role="img" aria-label="Photo of basic relaxation posture with a bolster under the knees"></div>
    <h2><b>POSTURE 5</b> – Basic Relaxation Posture with Knee Support</h2>
    <div class="posture-body">
      <p><span class="label">PROPS</span> – 1 x bolsters (or 1 x bed pillows or rolled up towel)</p>
      <p><span class="label">SET UP NOTES</span> – Reclining on back, position bolster or pillows under knees.</p>
    </div>
  </article>

  <p class="quote q1"><span class="mark">“</span>Tension is who you think you are, Relaxation is who you actually are”</p>
  <p class="quote q2"><span class="mark">“</span>Life isn't as serious as the mind makes it out to be” —Oren Hale</p>
</section>

</body>
</html>
```